Poster for our band

We need a logo and poster designing for us to send to the venues we are performing at. Our band is called "Brisk"
Can use different backgrounds to make poster look more Arty
We would like the poster to look contemporary, modern and unique. As many or as little pictures can be used that I will send.
We perform at Holiday Parks, Hotels etc so the Poster needs to look classy and sophisticated.Can be Portrait or Landscape. Poster could be Black and White or Colour
A very creative Logo
Could contain the following script somewhere on the poster.

Performing hits by- The Drifters Nine, Two Harbours, Lend Over, Gordon Pellworth, Barons of Teme, Rafters, Q7, Marble Owls and many more.

Poster needs our website address.
www.thebandbrisk.example.co.uk

Poster needs our Agent Name and number

Represented by- ORV - 01632 960418

Target Market(s)

Holiday Parks
Hotels
Nightclubs
Bars

Industry/Entity Type

Landscape

Colors
000000

Requirements
Must have
• Can be Portrait or Landscape. Poster could be Black and White or Colour
A very creative Logo

www.thebandbrisk.example.co.uk

Nice to have
• Cool, Contemopoary, Modern design
Photos can be cut out or changed in anyway to make us look great.

```html
<!DOCTYPE html>
<html lang="en">
<head>
<meta charset="utf-8">
<title>Brisk – Band Poster</title>
<link rel="stylesheet" href="https://fonts.googleapis.com/css2?family=Open+Sans:wght@700&family=Saira+Extra+Condensed:wght@300;400&display=swap">
<style>
  :root {
    --page: #ffffff;
    --ink-dark: #141414;
    --smoke-mid: #4a4748;
    --smoke-light: #b9b6b9;
    --logo-white: #ececec;
    --copy-white: #ffffff;
    --web-gold: #e9b51d;
    --strip-dark: #1b1916;
    --strip-warm: #5a4a36;
  }
  * { margin: 0; padding: 0; box-sizing: border-box; }
  html, body {
    width: 1200px; height: 1000px; overflow: hidden;
    background: var(--page);
  }
  .canvas { position: relative; width: 1200px; height: 1000px; }

  .poster {
    position: absolute; left: 37px; top: 103px;
    width: 1134px; height: 802px; overflow: hidden;
    background:
      radial-gradient(ellipse 420px 380px at 330px 330px, #2a2828 0%, #3a3738 45%, rgba(70,66,68,0) 80%),
      radial-gradient(ellipse 600px 360px at 950px 80px, #c9c6ca 0%, rgba(160,156,160,0.5) 50%, rgba(0,0,0,0) 90%),
      linear-gradient(180deg, #3c393a 0%, var(--smoke-mid) 55%, #8e8a8d 90%, var(--smoke-light) 100%);
  }
  .backdrop-art { position: absolute; inset: 0; }

  .band-photo {
    position: absolute; left: 658px; top: 58px;
    width: 440px; height: 640px;
    background: radial-gradient(ellipse 220px 320px at 50% 55%, #1e1c1d 0%, #2d2a2b 55%, rgba(50,47,48,0) 100%);
  }

  .logo { position: absolute; left: 88px; top: 180px; }

  .setlist {
    position: absolute; left: 0; top: 556px; width: 1162px;
    text-align: center;
    font-family: "Open Sans", Arial, sans-serif; font-weight: 700;
    color: var(--copy-white);
    text-shadow: 1px 1px 3px rgba(0,0,0,0.8);
  }
  .setlist-heading { font-size: 23px; line-height: 38px; padding-left: 16px; }
  .setlist-names { font-size: 22px; line-height: 40px; }

  .contact-strip {
    position: absolute; left: 0; top: 705px; width: 1134px; height: 62px;
    background: linear-gradient(90deg, var(--strip-dark) 0%, #221e1a 45%, var(--strip-warm) 75%, #3a3026 100%);
  }
  .contact-text { position: absolute; inset: 0; }
</style>
</head>
<body>
<div class="canvas">
  <section class="poster">
    <svg class="backdrop-art" width="1134" height="802" role="img" aria-label="Abstract motion-blurred swirl photograph in black and grey tones">
      <defs>
        <radialGradient id="swirl" cx="330" cy="330" r="560" gradientUnits="userSpaceOnUse">
          <stop offset="0" stop-color="#1e1d1d" stop-opacity="0.6"/>
          <stop offset="0.5" stop-color="#555152" stop-opacity="0.25"/>
          <stop offset="1" stop-color="#9a969a" stop-opacity="0"/>
        </radialGradient>
      </defs>
      <rect width="1134" height="802" fill="url(#swirl)"/>
    </svg>

    <div class="band-photo" role="img" aria-label="Black and white photograph of the three band members standing against a dark wall"></div>

    <svg class="logo" width="640" height="340" aria-label="Brisk">
      <text x="2" y="322" textLength="588" lengthAdjust="spacingAndGlyphs"
            font-family="'Saira Extra Condensed', 'Arial Narrow', sans-serif"
            font-weight="300" font-size="430" fill="#ececec">BRISK</text>
    </svg>

    <div class="setlist">
      <p class="setlist-heading">- Performing hits by -</p>
      <p class="setlist-names">The Drifters Nine, Two Harbours, Lend Over, Gordon Pellworth, Barons of Teme, Rafters,</p>
      <p class="setlist-names">Q7, Marble Owls and many more.</p>
    </div>

    <div class="contact-strip">
      <svg class="contact-text" width="1134" height="62">
        <text class="agent" x="125" y="44" textLength="470" lengthAdjust="spacingAndGlyphs"
              font-family="'Saira Extra Condensed', 'Arial Narrow', sans-serif"
              font-weight="400" font-size="32" fill="#ffffff">Represented by- ORV - 01632 960418</text>
        <text class="website" x="640" y="43" textLength="440" lengthAdjust="spacingAndGlyphs"
              font-family="'Saira Extra Condensed', 'Arial Narrow', sans-serif"
              font-weight="400" font-size="34" fill="#e9b51d">www.thebandbrisk.example.co.uk</text>
      </svg>
    </div>
  </section>
</div>
</body>
</html>
```